I'm looking for a smart new design for business cards

Industry/Entity Type

Commercial Electrical

Contact Information for Business Card

Logo, name, email, position, website QR

Requirements
Nice to have
• Logo embedded behind the text side

```html
<!DOCTYPE html>
<html lang="en">
<head>
<meta charset="utf-8">
<title>Northline Power Contractors – Business Card</title>
<link href="https://fonts.googleapis.com/css2?family=Montserrat:wght@400;500;700;800&display=swap" rel="stylesheet">
<style>
  :root {
    --bg: #969696;
    --card: #ffffff;
    --navy: #2b2d78;
    --red: #dc1e2b;
    --ink: #111111;
    --text: #3a3a3a;
  }
  * { margin: 0; padding: 0; box-sizing: border-box; }
  html, body { width: 1200px; height: 1108px; overflow: hidden; }
  body {
    background: var(--bg);
    font-family: "Montserrat", Arial, sans-serif;
    position: relative;
  }
  .card {
    position: absolute;
    left: 242px;
    width: 716px;
    height: 410px;
    background: var(--card);
    border-radius: 36px;
  }
  .card--front { top: 119px; }
  .card--back { top: 580px; }

  .brand {
    position: absolute;
    display: flex;
    align-items: center;
    gap: 18px;
  }
  .brand__square {
    flex: none;
    background: var(--red);
  }
  .brand__name {
    color: var(--navy);
    font-weight: 800;
    text-transform: uppercase;
    line-height: 1.1;
    letter-spacing: 0.5px;
  }
  .card--front .brand {
    left: 0; right: 0; top: 118px;
    justify-content: center;
  }
  .card--front .brand__square { width: 64px; height: 64px; }
  .card--front .brand__name { font-size: 38px; }

  .card--back .brand { left: 50px; top: 158px; width: 300px; gap: 12px; }
  .card--back .brand__square { width: 36px; height: 36px; }
  .card--back .brand__name { font-size: 21px; }

  .divider {
    position: absolute;
    left: 370px; top: 94px;
    width: 2px; height: 221px;
    background: var(--red);
  }
  .contact {
    position: absolute;
    left: 400px; top: 86px;
  }
  .contact__name {
    font-size: 34px;
    font-weight: 700;
    color: var(--navy);
    line-height: 1.1;
  }
  .contact__name .surname { color: var(--red); }
  .contact__role {
    font-size: 18px;
    color: var(--text);
    margin-top: 6px;
  }
  .contact__address {
    font-size: 18px;
    color: var(--text);
    line-height: 29px;
    margin-top: 14px;
    font-style: normal;
  }
  .contact__list {
    list-style: none;
    margin-top: 9px;
  }
  .contact__item {
    display: flex;
    align-items: center;
    gap: 8px;
    font-size: 18px;
    color: var(--text);
    height: 28.5px;
  }
  .contact__icon { width: 16px; height: 16px; fill: var(--red); flex: none; }
</style>
</head>
<body>
  <section class="card card--front">
    <div class="brand">
      <span class="brand__square"></span>
      <span class="brand__name">Northline Power<br>Contractors</span>
    </div>
  </section>

  <section class="card card--back">
    <div class="brand">
      <span class="brand__square"></span>
      <span class="brand__name">Northline Power<br>Contractors</span>
    </div>

    <div class="divider"></div>

    <div class="contact">
      <h1 class="contact__name">Daniel <span class="surname">Hartley</span></h1>
      <p class="contact__role">Managing Director</p>
      <address class="contact__address">Your address, City<br>State, Zip 1234</address>
      <ul class="contact__list">
        <li class="contact__item">
          <svg class="contact__icon" viewBox="0 0 16 16"><path d="M1 6c0-2 3-3.5 7-3.5S15 4 15 6v1.5h-3.5V5.8C10.5 5.4 9.3 5.2 8 5.2s-2.5.2-3.5.6v1.7H1z"/><path d="M4 8.5h8l1.5 5h-11z"/></svg>
          123 456 789
        </li>
        <li class="contact__item">
          <svg class="contact__icon" viewBox="0 0 16 16"><path d="M1 3.5h14v9H1z M1.8 4.2 8 9l6.2-4.8" stroke="#fff" stroke-width="1"/></svg>
          info@youremail.com
        </li>
        <li class="contact__item">
          <svg class="contact__icon" viewBox="0 0 16 16"><circle cx="8" cy="8" r="7"/><path d="M1 8h14M8 1c-3 3.5-3 10.5 0 14M8 1c3 3.5 3 10.5 0 14" stroke="#fff" stroke-width="1" fill="none"/></svg>
          www.yourwebsite.com
        </li>
      </ul>
    </div>
  </section>
</body>
</html>
```